Corvane Business Cards

Front of business card will have logo, name, address, & telephone number. Back of card will have a list of services provided - Roads, Substation Pads, Temporary Pads, Site Pads, Land Leveling, Powerline Row Cleaning, Land Clearing, Gates, Fencing, Construction Entrances, Excavation, Trenching, Underground Utilities, Directional Boring, Pile Driving. We are a construction company that uses heavy equipment like bulldozers, motor graders/blades, dump trucks, backhoes, hydro axes, & skid loaders. We build roads, pads, & install electric utility lines & waterlines underground. This logo is new. The word "Construction" can be smaller as uploaded 2 example edited logos. We will be using this card design for many employees.
Target Market(s)
Industrial Electric Powerline, Wind Turbine, Solar Panel, & Water Utility companies.
Contact Information for Business Card
Name/Position - Dwayne Halster - Owner
Address: 4875 FM 309
Dunmore, OK 73812
Phone number - (580) 482-5096

```html
<!DOCTYPE html>
<html lang="en">
<head>
<meta charset="utf-8">
<title>Corvane Business Cards</title>
<link rel="stylesheet" href="https://fonts.googleapis.com/css2?family=Marcellus&family=Oswald:wght@500&family=Arimo&display=swap">
<style>
  :root {
    --bg: #e4e4e4;
    --card-white: #ffffff;
    --maroon: #3b1119;
    --ink: #1c1c1c;
    --light: #f4ecee;
    --rule: rgba(255,255,255,0.35);
  }
  * { margin: 0; padding: 0; box-sizing: border-box; }
  html, body { width: 1200px; height: 802px; overflow: hidden; }
  body { background: var(--bg); position: relative; font-family: "Arimo", Arial, sans-serif; }

  .card { position: absolute; top: 274px; width: 443px; height: 264px; }
  .card-front { left: 136px; background: var(--card-white); }
  .card-back { left: 624px; background: var(--maroon); color: var(--light); text-align: center; }

  .holder-name {
    position: absolute; left: 32px; top: 28px;
    font-family: "Marcellus", serif; font-size: 19px; line-height: 22px; letter-spacing: 1.5px;
    color: var(--maroon); text-transform: uppercase; white-space: nowrap;
  }
  .holder-role { position: absolute; left: 32px; top: 53px; font-size: 12px; line-height: 14px; color: var(--ink); }

  .brand {
    position: absolute; left: 214px; top: 74px; width: 206px;
    font-family: "Marcellus", serif; color: var(--maroon); text-align: center; white-space: nowrap;
  }
  .brand-name { display: block; font-size: 34px; line-height: 34px; letter-spacing: 2px; }
  .brand-sub { display: block; font-size: 21px; line-height: 24px; letter-spacing: 0.3px; margin-top: 42px; }

  .address {
    position: absolute; left: 32px; top: 209px;
    font-size: 12.5px; line-height: 16.5px; color: var(--ink); white-space: nowrap;
  }
  .phone {
    position: absolute; right: 34px; top: 221px;
    font-family: "Oswald", sans-serif; font-weight: 500; font-size: 15px; line-height: 20px; color: var(--ink);
  }
  .front-band { position: absolute; left: 0; bottom: 0; width: 100%; height: 8px; background: var(--maroon); }

  .services, .about, .summary { font-size: 12.6px; line-height: 16.5px; white-space: nowrap; }
  .services { margin-top: 34px; }
  .divider { width: 186px; height: 1px; background: var(--rule); margin: 11px auto 14px; }
</style>
</head>
<body>
  <section class="card card-front" aria-label="Business card front">
    <p class="holder-name">Dwayne Halster</p>
    <p class="holder-role">Owner</p>
    <div class="brand">
      <span class="brand-name">CORVANE</span>
      <span class="brand-sub">CONSTRUCTION</span>
    </div>
    <p class="address">4875 FM 309<br>Dunmore, OK 73812</p>
    <p class="phone">(580) 482-5096</p>
    <div class="front-band"></div>
  </section>

  <section class="card card-back" aria-label="Business card back">
    <p class="services">
      Roads, Substation Pads | Temporary Pads | Site Pads,<br>
      Land Leveling | Powerline Row Cleaning | Land Clearing<br>
      Gates | Fencing,Construction Entrances | Excavation<br>
      Trenching | Underground Utilities | Directional Boring | Pile Driving.
    </p>
    <div class="divider"></div>
    <p class="about">
      We are a construction company that uses heavy equipment<br>
      like bulldozers | motor graders/blades | dump trucks<br>
      backhoes | hydro axes &amp; skid loaders.
    </p>
    <div class="divider"></div>
    <p class="summary">
      We build roads, pads<br>
      install electric utility lines &amp; waterlines underground.
    </p>
  </section>
</body>
</html>
```